TVL 25 year Anniversary - create file

I need an electronic Image file that I can incorporate into everything we are dong -including our pamphlets and brochures which we print in-house with Word Or Publisher files

The Vexo guide 25 file attached is the look we're after for part of our 25 year branding. I've included three of our different operating brands that should be incorporated into the letters. Other facts that can be included are :
123 combined years of experience
11792 Clients on file
11 Team Members
60% have been with us 5+ years
Service Entire Niagara Region
Carpet Cleaning
Oriental Rug Cleaning
Rug Binding
Making Custom Rugs
Winner of 8 Franchise Awards
Winner - Chamber of Commerce - "Excellence in Business"
Winner - Kestrel Outreach's "Rise Past Goals " Award
Marisol and Gus featured in magazine article "Wedded to Commerce"
Supporters of the "Kids" programs at the QRSB
Supporters of our Local Health System

Industry/Entity Type

Electronic

Colors
0255a3

Requirements
Must have
• final file must be a format that I can use to insert into other publications in Word and Publisher

```html
<!DOCTYPE html>
<html lang="en">
<head>
<meta charset="utf-8">
<title>TVL 25 Year Anniversary</title>
<link href="https://fonts.googleapis.com/css2?family=PT+Sans:wght@400;700&display=swap" rel="stylesheet">
<style>
  :root {
    --stage: #2b2b2b;
    --brand-blue: #0255a3;
    --panel-light: #1f80c8;
    --panel-dark: #0a4f9e;
    --numeral-fill: #f3f4f7;
    --numeral-edge: #2a2f6e;
    --ink: #0d55a5;
    --icon-grey: #6b6b6b;
  }
  * { margin: 0; padding: 0; box-sizing: border-box; }
  html, body { width: 1200px; height: 1000px; overflow: hidden; background: var(--stage); }
  body { font-family: "PT Sans", sans-serif; color: var(--ink); }
  .canvas { position: relative; width: 1200px; height: 1000px; }
  .anniversary-panel {
    position: absolute; left: 116px; top: 127px; width: 1001px; height: 705px;
    background: radial-gradient(ellipse at 55% 45%, var(--panel-light) 0%, var(--panel-dark) 80%);
  }
  .numerals { position: absolute; left: 0; top: 0; width: 1200px; height: 1000px; }
  .numeral { fill: var(--numeral-fill); stroke: var(--numeral-edge); stroke-width: 2; stroke-linejoin: round; filter: drop-shadow(0 2px 3px rgba(0,0,0,.35)); }
  .icon { fill: var(--icon-grey); }
  .t { position: absolute; line-height: 1.1; white-space: nowrap; }
  .c { transform: translateX(-50%); text-align: center; }
  .b { font-weight: 700; }
  .brand-name { font-weight: 700; color: var(--brand-blue); }
</style>
</head>
<body>
<div class="canvas">
  <div class="anniversary-panel"></div>

  <svg class="numerals" viewBox="0 0 1200 1000" width="1200" height="1000">
    <path class="numeral numeral-two" d="M200,355 L200,320 C200,235 290,168 395,168 C510,168 590,245 590,330 C590,395 560,440 515,490 L335,645 L580,645 L580,740 L195,740 L195,690 L400,470 C450,415 470,385 470,330 C470,280 440,245 400,245 C355,245 320,280 320,355 Z"/>
    <path class="numeral numeral-five" d="M665,178 L1005,178 L1005,272 L775,272 L775,370 C815,350 860,340 900,340 C985,340 1035,440 1035,550 C1035,670 950,750 840,750 C750,750 680,710 645,665 L645,570 L770,570 C790,625 820,650 855,650 C900,650 920,610 920,570 C920,520 885,490 845,490 L665,490 Z"/>

    <rect class="icon" x="246" y="252" width="62" height="30" rx="12" role="img" aria-label="Handshake icon"/>
    <rect class="icon" x="464" y="205" width="66" height="78" rx="10" role="img" aria-label="Trophy with stars icon"/>
    <rect class="icon" x="425" y="445" width="90" height="30" rx="8" role="img" aria-label="Team member figures"/>
    <rect class="icon" x="390" y="485" width="90" height="30" rx="8" role="img" aria-label="Team member figures"/>
    <rect class="icon" x="335" y="525" width="95" height="30" rx="8" role="img" aria-label="Team member figures"/>
    <rect class="icon" x="315" y="565" width="55" height="30" rx="8" role="img" aria-label="Team member figures"/>
    <rect class="icon" x="258" y="672" width="30" height="28" rx="6" role="img" aria-label="Thumbs up icon"/>
    <rect class="icon" x="508" y="680" width="64" height="56" rx="10" role="img" aria-label="Two children figures"/>
    <rect class="icon" x="692" y="190" width="72" height="72" rx="36" role="img" aria-label="Laurel wreath number one award icon"/>
    <rect class="icon" x="780" y="378" width="60" height="60" rx="12" role="img" aria-label="Rolled carpet icon"/>
    <rect class="icon" x="935" y="585" width="55" height="70" rx="12" role="img" aria-label="Award ribbon number one icon"/>
  </svg>

  <div class="t brand-name" style="left:318px;top:196px;font-size:40px;">TVL</div>
  <div class="t brand-name" style="left:324px;top:686px;font-size:14px;">Loom Rinse Co</div>
  <div class="t brand-name c" style="left:700px;top:596px;font-size:15px;">Weave Room<br>Studio</div>

  <div class="t b" style="left:217px;top:295px;font-size:33px;">11792</div>
  <div class="t" style="left:222px;top:333px;font-size:15px;">Clients on file</div>

  <div class="t c" style="left:522px;top:292px;font-size:21px;"><span class="b" style="font-size:26px;">Winner</span><br>of 8<br>Franchise<br>Awards</div>

  <div class="t b c" style="left:491px;top:390px;font-size:32px;">11</div>
  <div class="t c" style="left:490px;top:425px;font-size:15px;">Team Members</div>

  <div class="t b" style="left:255px;top:598px;font-size:40px;">123</div>
  <div class="t" style="left:247px;top:636px;font-size:14px;">combined</div>
  <div class="t" style="left:221px;top:654px;font-size:14px;">years of experience</div>

  <div class="t c" style="left:262px;top:706px;font-size:14px;">Supporters of our<br>Local Health System</div>
  <div class="t" style="left:412px;top:655px;font-size:15px;">Supporters of the "Kids"<br>programs<br>at the<br>QRSB</div>

  <div class="t b c" style="left:880px;top:183px;font-size:35px;">Winner</div>
  <div class="t c" style="left:885px;top:222px;font-size:18px;">Kestrel Outreach's<br>"Rise Past Goals" Award</div>

  <div class="t b" style="left:683px;top:274px;font-size:37px;">60%</div>
  <div class="t c" style="left:725px;top:318px;font-size:19px;">have been<br>with us</div>
  <div class="t b c" style="left:727px;top:370px;font-size:23px;">5+ years</div>

  <div class="t" style="left:851px;top:387px;font-size:15px;">Carpet Cleaning</div>
  <div class="t c" style="left:932px;top:422px;font-size:15px;">Oriental Rug<br>Cleaning</div>
  <div class="t c" style="left:720px;top:414px;font-size:15px;">Making<br>Custom Rugs</div>
  <div class="t" style="left:676px;top:456px;font-size:15px;">Rug Binding</div>

  <div class="t b c" style="left:966px;top:462px;font-size:29px;">Winner</div>
  <div class="t c" style="left:982px;top:500px;font-size:16px;">Chamber of<br>Commerce<br>"Excellence in<br>Business"</div>

  <div class="t c" style="left:728px;top:642px;font-size:14px;">Service Entire<br>Niagara<br>Region</div>

  <div class="t b c" style="left:855px;top:668px;font-size:22px;">Marisol and Gus</div>
  <div class="t c" style="left:852px;top:697px;font-size:14px;">featured in magazine article<br>"Wedded to Commerce"</div>
</div>
</body>
</html>
```